Business Card Design

Hi I need a business card designed, we already have the business name logo artwork and would like some concept ideas for the Bus Card layout.
On the back of the card i want to include the products and services that we offer.
We are a Plastics Sheeting manufacture based in Perth Australia.

                                       

We need a BC design for a company called Tarvo Plastics based in Perth Australia.

We supply from DIY to Trade & Industrial  Engineering Markets.

We specialise in:

·         Cut to size panels  (all shapes and sizes)

·         Plastics fabrication & Welding

·         Custom Designs

·         Plastic Repairs

·         PVC Pipe Slotting & PVC Pipe Threading

·         Supplier of all types of engineering plastics and profiles.

Including:           Acrylic / Clarvene

                               Polycarbonate / Dorvil

                               Prismatic Light Diffuser

                               Vantrib

                               HDPE / UHMWPE

                               PVC / PVC Foam

                               Nylon

                               HIPS

```html
<!DOCTYPE html>
<html lang="en">
<head>
<meta charset="utf-8">
<title>Tarvo Plastics – Business Card</title>
<link rel="stylesheet" href="https://fonts.googleapis.com/css2?family=Source+Sans+3:wght@400;600;700&display=swap">
<style>
  :root {
    --page-bg: #e9e6e1;
    --navy: #1f2f6b;
    --navy-deep: #18265a;
    --sky: #2a8fcf;
    --white: #ffffff;
    --steel-light: #e4e6e8;
    --steel-mid: #b7bbbf;
    --steel-dark: #55595e;
    --steel-shadow: #2e3135;
  }
  * { box-sizing: border-box; margin: 0; padding: 0; }
  html, body { width: 1200px; height: 720px; overflow: hidden; }
  body {
    background: var(--page-bg);
    font-family: "Source Sans 3", "Myriad Pro", sans-serif;
    position: relative;
  }
  .card {
    position: absolute;
    top: 205px;
    width: 540px;
    height: 310px;
    overflow: hidden;
    box-shadow: 0 6px 18px rgba(0,0,0,0.18);
  }
  .card--front { left: 40px; }
  .card--back { left: 620px; }

  /* Front */
  .card--front {
    background: linear-gradient(100deg, var(--steel-mid) 0%, var(--steel-light) 35%, #cfd2d5 60%, var(--steel-light) 85%, var(--steel-mid) 100%);
  }
  .brand {
    position: absolute;
    left: 0; right: 0; top: 30px;
    display: flex; align-items: center; justify-content: center; gap: 12px;
  }
  .brand__mark {
    width: 26px; height: 26px;
    background: var(--navy);
  }
  .brand__name {
    font-size: 54px; font-weight: 700; color: var(--navy);
    letter-spacing: 0.5px; line-height: 1;
  }
  .band-sky {
    position: absolute; left: 0; right: 0; top: 110px; height: 28px;
    background: var(--sky);
  }
  .band-navy {
    position: absolute; left: 0; right: 0; top: 138px; bottom: 0;
    background: var(--navy);
    color: var(--white);
    text-align: center;
    padding-top: 10px;
  }
  .person { font-size: 19px; font-weight: 400; margin-bottom: 14px; }
  .person strong { font-weight: 700; }
  .contact-line {
    font-size: 14.5px; line-height: 1.45;
    display: flex; align-items: center; justify-content: center; gap: 6px;
  }
  .contact-line svg { width: 13px; height: 13px; fill: var(--white); flex: none; }
  .contact-line + .contact-line { margin-top: 2px; }

  /* Back */
  .card--back {
    background: linear-gradient(180deg, var(--steel-light) 0%, #c9ccd0 28%, var(--steel-dark) 72%, var(--steel-shadow) 100%);
    text-align: center;
    padding-top: 22px;
  }
  .offer-title {
    color: var(--navy); font-weight: 700; font-size: 16.5px; line-height: 1.25;
  }
  .section-heading {
    color: var(--white); font-weight: 700; font-size: 18px;
    margin-top: 14px; margin-bottom: 4px;
    text-shadow: 0 1px 2px rgba(0,0,0,0.35);
  }
  .item-list {
    list-style: none;
    color: var(--white); font-size: 14px; line-height: 1.5;
    text-shadow: 0 1px 2px rgba(0,0,0,0.4);
    padding: 0 30px;
  }
  .item-list li span { white-space: nowrap; }
  .item-list li span + span { margin-left: 12px; }
</style>
</head>
<body>

<section class="card card--front" aria-label="Business card front">
  <div class="brand">
    <span class="brand__mark"></span>
    <span class="brand__name">Tarvo Plastics</span>
  </div>
  <div class="band-sky"></div>
  <div class="band-navy">
    <p class="person"><strong>Your Name,</strong> Title</p>
    <p class="contact-line">
      <svg viewBox="0 0 16 16"><path d="M3.5 1l2.5 3-1.5 1.8c.8 1.9 2.3 3.4 4.2 4.2L10.5 8.5l3 2.5-1.5 3C6.5 13.5 2.5 9.5 2 4z"/></svg>
      08 9400 3115
      <svg viewBox="0 0 16 16"><rect x="4" y="1" width="8" height="14" rx="1.5"/></svg>
      123-456-7890
      <svg viewBox="0 0 16 16"><rect x="4" y="1" width="8" height="4"/><rect x="1" y="6" width="14" height="6" rx="1"/><rect x="4" y="10" width="8" height="5"/></svg>
      08 9400 3126
    </p>
    <p class="contact-line">sales@tarvoplastics.com.au &nbsp;|&nbsp; Korrin Holdings Pty Ltd T/A Tarvo Plastics ABN: TBA</p>
    <p class="contact-line">Unit 4/18 Brindle Court Harlow Vale WA 6155</p>
    <p class="contact-line">
      <svg viewBox="0 0 16 16"><path d="M1 3h14v10H1z M1 3l7 6 7-6" fill="none" stroke="#fff" stroke-width="1.6"/></svg>
      PO Box 2270 Harlow Vale DC WA 6970
    </p>
  </div>
</section>

<section class="card card--back" aria-label="Business card back">
  <h2 class="offer-title">The Products And Services That We Offer<br>Are Supplied From Diy To Trade &amp; Industrial Engineering Markets</h2>
  <h3 class="section-heading">We specialise in:</h3>
  <ul class="item-list">
    <li><span>• Cut to size panels (all shapes and sizes)</span></li>
    <li><span>• Plastics fabrication &amp; Welding</span><span>• Custom Designs</span></li>
    <li><span>• Plastic Repairs</span><span>• PVC Pipe Slotting &amp; PVC Pipe Threading</span></li>
    <li><span>• Supplier of all types of engineering plastics and profiles</span></li>
  </ul>
  <h3 class="section-heading">Including:</h3>
  <ul class="item-list">
    <li><span>• Acrylic / Clarvene</span><span>• Polycarbonate / Dorvil</span></li>
    <li><span>• Prismatic Light Diffuser</span><span>• Vantrib</span><span>• HDPE / UHMWPE</span></li>
    <li><span>• PVC / PVC Foam</span><span>• Nylon</span><span>• HIPS</span></li>
  </ul>
</section>

</body>
</html>
```